business card

Business card for new business.
Red and black corporate colors.
Card can have an Indsutrial feel to it. Feel free to add Rust, Bolted steel, or graphics as you see fit. We provide highly specialized services to the below mentioned industries.
Keep information out of corners so that if I want I can choose rounded corners.
Information
- front. name - title - phone - email
- Rear
Refining - Rail - Infrastructure - Mining - Energy
Calgary - Edmonton - Fort McMurray - Revelstoke - Vancouver

```html
<!DOCTYPE html>
<html lang="en">
<head>
<meta charset="UTF-8">
<title>Ironvale Business Card</title>
<link href="https://fonts.googleapis.com/css2?family=Arimo:wght@400;700&display=swap" rel="stylesheet">
<style>
  :root {
    --backdrop: #1b1b1e;
    --card: #25272a;
    --ink-grey: #8c8f93;
    --ink-light: #a9acb0;
    --accent-red: #e0212a;
  }
  * { margin: 0; padding: 0; box-sizing: border-box; }
  html, body {
    width: 1200px; height: 800px; overflow: hidden;
    background: var(--backdrop);
    font-family: "Arimo", Arial, sans-serif;
  }
  .canvas {
    position: relative; width: 1200px; height: 800px;
  }
  .card {
    position: absolute;
    width: 560px; height: 320px;
    background: var(--card);
    box-shadow: 0 18px 40px rgba(0,0,0,0.55);
  }
  .card-front { left: 90px; top: 70px; }
  .card-back { left: 550px; top: 410px; }

  .brand {
    position: absolute; left: 50%; top: 50%;
    transform: translate(-50%, -50%);
    display: flex; align-items: center; gap: 14px;
  }
  .brand-square {
    width: 22px; height: 22px; background: var(--accent-red);
  }
  .brand-name {
    font-weight: 700; font-size: 54px; letter-spacing: 2px;
    color: var(--ink-grey);
  }

  .person {
    position: absolute; left: 56px; top: 92px; width: 190px; text-align: right;
  }
  .person-name {
    font-weight: 700; font-size: 19px; color: var(--ink-grey);
  }
  .person-title {
    font-size: 15px; color: var(--accent-red); margin-top: 3px;
  }
  .divider {
    position: absolute; left: 268px; top: 82px;
    width: 1px; height: 68px; background: var(--accent-red);
  }
  .contact {
    position: absolute; left: 290px; top: 80px;
    list-style: none;
  }
  .contact li {
    display: flex; align-items: center; gap: 10px;
    font-size: 14px; color: var(--ink-grey); line-height: 24px;
  }
  .contact svg { width: 14px; height: 14px; flex: none; }

  .coverage {
    position: absolute; left: 56px; right: 56px; bottom: 62px;
    font-size: 14px; color: var(--ink-grey); line-height: 24px;
  }
  .coverage .sep { color: var(--accent-red); padding: 0 5px; }
</style>
</head>
<body>
<main class="canvas">
  <section class="card card-front">
    <div class="brand">
      <span class="brand-square"></span>
      <span class="brand-name">IRONVALE</span>
    </div>
  </section>

  <section class="card card-back">
    <div class="person">
      <p class="person-name">Daniel Reyes</p>
      <p class="person-title">Managing Director</p>
    </div>
    <div class="divider"></div>
    <ul class="contact">
      <li>
        <svg viewBox="0 0 14 14"><rect x="1.5" y="1.5" width="11" height="11" fill="none" stroke="#e0212a" stroke-width="1.8"/></svg>
        (01) 5550 1472
      </li>
      <li>
        <svg viewBox="0 0 14 14"><rect x="0" y="0" width="14" height="14" fill="#e0212a"/><path d="M3 7.5 L6 10 L11 4" fill="none" stroke="#25272a" stroke-width="1.8"/></svg>
        info@ironvale.com
      </li>
      <li>
        <svg viewBox="0 0 14 14"><circle cx="7" cy="7" r="6.5" fill="#e0212a"/><path d="M0.5 7 H13.5 M7 0.5 V13.5 M2 3.5 H12 M2 10.5 H12" stroke="#25272a" stroke-width="0.9" fill="none"/><ellipse cx="7" cy="7" rx="3" ry="6.5" fill="none" stroke="#25272a" stroke-width="0.9"/></svg>
        www.ironvale.com
      </li>
    </ul>
    <div class="coverage">
      <p class="industries">Refining<span class="sep">|</span>Rail<span class="sep">|</span>Infrastructure<span class="sep">|</span>Mining<span class="sep">|</span>Energy</p>
      <p class="locations">Calgary<span class="sep">|</span>Edmonton<span class="sep">|</span>Fort McMurray<span class="sep">|</span>Revelstoke<span class="sep">|</span>Vancouver</p>
    </div>
  </section>
</main>
</body>
</html>
```